Copper Moth Bar & Grill Takeout Menu

Please create a takeout menu using the attached dine-in menu.
Take out menu size: Tri-Fold 11x17

Industry/Entity Type

Bar & Grill (Restaurant)

Colors

Designer to choose colors to be used in the design.

Requirements
Must have
• Phone number and website. "Order Online" "Order for Delivery"
Nice to have
• Area on the back of the menu to feature happy hour specials.

```html
<!DOCTYPE html>
<html lang="en">
<head>
<meta charset="utf-8">
<title>Copper Moth Bar &amp; Grill — Takeout Menu</title>
<link rel="stylesheet" href="https://fonts.googleapis.com/css2?family=Almendra:ital,wght@0,400;0,700;1,400;1,700&family=Alegreya+SC:wght@700;800&family=Dosis:wght@300;400;600;700&display=swap">
<style>
:root{
  --backdrop:#adc4d0;
  --paper:#ffffff;
  --red:#d9432e;
  --cover-red:#d2362a;
  --deep-red:#c7301f;
  --yellow:#e8e45a;
  --blue:#3c3192;
  --green:#5aa62f;
  --ink:#2b2b2b;
}
*{margin:0;padding:0;box-sizing:border-box}
html,body{width:926px;height:1200px;overflow:hidden}
body{background:var(--backdrop);position:relative;font-family:"Dosis",sans-serif;color:var(--ink)}
.sheet{position:absolute;left:54px;width:817px;height:529px;background:var(--paper)}
.sheet--outside{top:56px}
.sheet--inside{top:614px}
.panel{position:absolute;top:0;width:273px;height:529px}
.panel--salads{left:0}
.panel--starters{left:272px;background:var(--red);color:#fff}
.panel--fries{left:544px}
.panel--cover{left:544px;background:var(--cover-red)}
.abs{position:absolute}
.art{position:absolute;border-radius:6px}

/* cover */
.brand{position:absolute;left:0;width:273px;top:26px;text-align:center;font-family:"Almendra",serif;font-weight:700;color:var(--yellow);font-size:34px;line-height:1.15}
.brand__sub{position:absolute;left:0;width:273px;top:134px;text-align:center;font-family:"Almendra",serif;font-weight:700;color:var(--yellow);font-size:20px}
.rule{position:absolute;left:60px;width:152px;height:3px;background:#fff;border-radius:2px}
.cover-title{position:absolute;left:0;width:273px;top:188px;text-align:center;font-family:"Almendra",serif;font-weight:700;color:#fff;font-size:62px;line-height:1}
.cover-scene{left:3px;top:280px;width:270px;height:200px;background:linear-gradient(180deg,#d2362a 0%,#c94a45 55%,#e0a39a 100%)}
.cover-order{position:absolute;left:0;width:273px;top:484px;text-align:center;font-family:"Dosis",sans-serif;font-weight:700;color:var(--blue);font-size:18px;word-spacing:6px}
.cover-web{position:absolute;left:0;width:273px;top:507px;text-align:center;font-weight:600;color:var(--blue);font-size:9.5px;letter-spacing:1px}

/* shared */
.banner{position:absolute;border-radius:14px 22px 12px 24px;font-family:"Alegreya SC",serif;font-weight:800;text-align:center;line-height:1}
.tick{display:inline-block;width:4px;height:8px;border-right:2px solid var(--green);border-bottom:2px solid var(--green);transform:rotate(40deg);margin:0 4px 2px 1px;vertical-align:middle}
.tick--gold{border-color:var(--yellow)}
.price{display:inline-block;background:var(--yellow);color:var(--red);font-size:11px;font-weight:600;padding:0 2px;line-height:13px}

/* salads */
.salad{position:absolute;left:24px;width:217px}
.salad__head{display:flex;align-items:baseline;font-family:"Almendra",serif;font-style:italic;font-weight:700;color:var(--blue);font-size:13.5px}
.salad__head .tick{position:absolute;left:-12px;top:6px}
.leader{flex:1;border-bottom:2px dotted var(--blue);margin:0 2px 3px}
.salad__price{font-family:"Almendra",serif;font-weight:700;font-style:normal}
.salad__desc{font-size:7px;line-height:1.25;color:#333;margin-top:1px}
.addons{left:24px;top:396px;width:188px;height:115px;border:3px solid var(--yellow);border-radius:20px;overflow:hidden;background:#fff}
.addons__list{position:absolute;left:14px;top:8px;width:162px;height:50px;border:1px solid var(--blue);border-bottom:none;border-radius:40px 40px 0 0}
.addons__dress{position:absolute;left:14px;top:58px;width:162px;height:48px;background:var(--blue);border-radius:0 0 40px 40px;color:#fff}
.vlabel{position:absolute;left:6px;font-family:"Almendra",serif;font-style:italic;font-weight:700;font-size:9px;transform:rotate(-90deg);transform-origin:left top}
.addons__rows{position:absolute;left:26px;top:9px;font-size:6.5px;line-height:1.35;color:#333;width:88px}
.addons__rows div{display:flex}
.addons__rows .leader{border-width:1px;border-color:#555;margin-bottom:2px}
.addons__dress p{position:absolute;left:26px;top:6px;width:108px;font-size:6.2px;line-height:1.3}

/* starters */
.section-title{position:absolute;font-family:"Alegreya SC",serif;font-weight:700;font-size:13px;letter-spacing:.5px}
.opt{position:absolute;font-size:9.5px;line-height:1.05;font-weight:400}
.opt .price{position:absolute;top:3px}
.quesa{left:16px;top:168px;width:234px;height:136px;border:1px solid var(--yellow);border-radius:4px;overflow:hidden}
.quesa__fill{position:absolute;left:0;top:0;width:100%;height:97px;background:var(--yellow)}
.quesa .opt{color:var(--ink)}
.quesa__note{position:absolute;left:8px;top:103px;width:218px;font-size:7px;line-height:1.2;color:var(--yellow)}
.nacho-box{left:20px;top:336px;width:226px;height:44px;border:1px solid #fff}
.nacho-box p{position:absolute;left:9px;top:6px;width:208px;font-size:7px;line-height:1.2}
.nacho-opt{font-size:9px}
.wings-desc{left:28px;top:484px;width:210px;font-size:7px;line-height:1.25}

/* fries */
.fries-frame{left:11px;top:22px;width:247px;height:157px;border:3px solid var(--red);border-radius:8px}
.fries-box{left:43px;top:30px;width:185px;height:142px;background:var(--red);color:#fff;border-radius:4px}
.fries-note{left:108px;top:3px;width:72px;font-size:6.3px;line-height:1.05;color:var(--yellow)}
.soup{position:absolute;left:24px;width:236px}
.soup__head{display:flex;align-items:baseline;font-family:"Almendra",serif;font-style:italic;font-weight:700;color:var(--blue);font-size:12.5px;white-space:nowrap}
.soup__head .tick{position:absolute;left:-13px;top:6px}
.soup__desc{font-size:7px;line-height:1.25;color:#333;margin-top:1px}
.soup-add{left:25px;top:418px;width:233px;height:37px;background:var(--yellow);border-radius:4px 4px 0 0}
.soup-add span{position:absolute;left:10px;top:9px;font-family:"Almendra",serif;font-style:italic;font-weight:700;font-size:14px;color:var(--red)}
.soup-add em{position:absolute;left:40px;top:13px;font-style:normal;font-size:7.5px;color:#333}
.notice{left:25px;top:455px;width:233px;height:60px;background:var(--blue);border-radius:0 0 4px 4px;color:#fff}
.notice p{position:absolute;left:10px;top:12px;width:214px;font-size:5.5px;line-height:1.4}
</style>
</head>
<body>

<section class="sheet sheet--outside" aria-label="Menu outside">
  <div class="panel panel--cover">
    <div class="brand">Copper<br>Moth</div>
    <div class="brand__sub">Bar &amp; Grill</div>
    <div class="rule" style="top:186px"></div>
    <h1 class="cover-title">Menu</h1>
    <div class="rule" style="top:270px"></div>
    <div class="art cover-scene" role="img" aria-label="Painted illustration of bar patrons drinking at a wooden counter with a burger plate"></div>
    <div class="cover-order">Order Delivery</div>
    <div class="cover-web">www.coppermothgrill.com</div>
  </div>
</section>

<section class="sheet sheet--inside" aria-label="Menu inside">

  <div class="panel panel--salads">
    <div class="banner" style="left:10px;top:26px;width:137px;height:40px;background:var(--yellow);color:var(--blue);font-size:25px;padding-top:7px">SALADS</div>
    <div class="art" style="left:168px;top:20px;width:77px;height:99px;background:radial-gradient(circle,#e4e2f2,#fff)" role="img" aria-label="Line sketch of a tossed salad bowl"></div>

    <div class="salad" style="top:94px;width:135px">
      <div class="salad__head">Combo Moth<span class="leader"></span><span class="salad__price">11</span></div>
      <p class="salad__desc">Enjoy a side House and a cup of any soup</p>
    </div>
    <div class="salad" style="top:131px">
      <div class="salad__head"><span class="tick"></span>Moth House Salad<span class="leader"></span><span class="salad__price">11</span></div>
      <p class="salad__desc">Spring lettuce mix, fresh red peppers, onion, cherry tomatoes,<br>cucumber, and croutons. Served with Red Wine Vinaigrette</p>
    </div>
    <div class="salad" style="top:176px">
      <div class="salad__head">Grilled Chicken Salad<span class="leader"></span><span class="salad__price">15</span></div>
      <p class="salad__desc">Spring lettuce mix, fresh red peppers, onion, cherry tomatoes,<br>cucumber, and croutons. Served with Red Wine Vinaigrette</p>
    </div>
    <div class="salad" style="top:221px">
      <div class="salad__head">Grilled Shrimp Salad*<span class="leader"></span><span class="salad__price">16</span></div>
      <p class="salad__desc">Spring lettuce mix, garlic roasted shrimp, roasted corn, pico de<br>gallo fresh avocado, Served with Lemon Champagne Vinaigrette</p>
    </div>
    <div class="salad" style="top:267px">
      <div class="salad__head"><span class="tick"></span>Goat Cheese Salad<span class="leader"></span><span class="salad__price">16</span></div>
      <p class="salad__desc">Spring lettuce mix, garlic roasted shrimp, roasted corn, pico de<br>gallo fresh avocado, Served with Lemon Champagne Vinaigrette</p>
    </div>
    <div class="salad" style="top:313px">
      <div class="salad__head"><span class="tick"></span>The Skinny Moth<span class="leader"></span><span class="salad__price">14</span></div>
      <p class="salad__desc">Spring lettuce mix, garlic roasted shrimp, roasted corn, pico de<br>gallo fresh avocado, Served with Lemon Champagne Vinaigrette</p>
    </div>
    <div class="salad" style="top:359px">
      <div class="salad__head"><span class="tick"></span>Small House Salad<span class="leader"></span><span class="salad__price">6</span></div>
      <p class="salad__desc">Spring lettuce mix, garlic roasted shrimp, roasted corn, pico de<br>gallo fresh avocado, Served with Lemon Champagne Vinaigrette</p>
    </div>

    <div class="abs addons">
      <div class="addons__list">
        <span class="vlabel" style="top:34px;color:var(--blue)">Add</span>
        <div class="addons__rows">
          <div>Grilled Chicken<span class="leader"></span>5</div>
          <div>Garlic Roasted Shrimp<span class="leader"></span>5</div>
          <div>Fried Goat Cheese<span class="leader"></span>4</div>
        </div>
      </div>
      <div class="addons__dress">
        <span class="vlabel" style="top:44px;color:var(--yellow)">Dressings</span>
        <p>Balsamic Vinaigrette | Caesar Red Wine Vinaigrette | Honey-Mustard | Lemon Champagne Vinaigrette | Ranch | Blue Cheese</p>
      </div>
    </div>
  </div>

  <div class="panel panel--starters">
    <div class="banner" style="left:20px;top:26px;width:173px;height:41px;background:#fff;color:var(--red);font-size:26px;padding-top:6px">STARTERS</div>
    <div class="art" style="left:160px;top:69px;width:100px;height:24px;background:radial-gradient(ellipse,#f0b8ac,var(--red))" role="img" aria-label="Line sketch of a plate of nachos"></div>

    <h2 class="section-title" style="left:26px;top:80px">TORTILLA CHIPS</h2>
    <div class="opt" style="left:12px;top:100px;width:100px"><span class="tick tick--gold"></span>with House-made<br><span style="padding-left:14px">Salsa Verde</span><span class="price" style="left:88px">7</span></div>
    <div class="opt" style="left:119px;top:100px;width:66px"><span class="tick tick--gold"></span>with<br><span style="padding-left:14px">Queso</span><span class="price" style="left:46px">8</span></div>
    <div class="opt" style="left:193px;top:100px;width:66px">with Chili<br>con Queso<span class="price" style="left:48px">9</span></div>
    <div class="opt" style="left:12px;top:133px;width:100px"><span class="tick tick--gold"></span>with Guacamole<br><span style="padding-left:14px">&amp; Pico De Gallo</span><span class="price" style="left:88px">8</span></div>
    <div class="opt" style="left:119px;top:133px;width:100px"><span class="tick tick--gold"></span>with House-made<br><span style="padding-left:14px">Fire Roasted Salsa</span><span class="price" style="left:92px">7</span></div>

    <div class="abs quesa">
      <div class="quesa__fill"></div>
      <h2 class="section-title" style="left:9px;top:6px;color:var(--red)">QUESADILLAS</h2>
      <div class="opt" style="left:9px;top:31px"><span class="tick"></span>Cheddar and<br><span style="padding-left:14px">Monterey Jack Cheese</span><span class="price" style="left:86px;top:0;background:var(--red);color:var(--yellow)">12</span></div>
      <div class="opt" style="left:128px;top:31px">Pulled Marinated<br>Chicken &amp; Cheese<span class="price" style="left:79px;top:0;background:var(--red);color:var(--yellow)">16</span></div>
      <div class="opt" style="left:9px;top:64px"><span class="tick"></span>Fire Roasted<br><span style="padding-left:14px">Vegetables and Cheese</span><span class="price" style="left:86px;top:0;background:var(--red);color:var(--yellow)">14</span></div>
      <div class="opt" style="left:128px;top:64px">Garlic Roasted<br>Shrimp &amp; Cheese<span class="price" style="left:79px;top:0;background:var(--red);color:var(--yellow)">16</span></div>
      <p class="quesa__note">All quesadillas are stuffed with roasted red peppers, black beans and your choice below. Served with guacamole, pico de gallo, &amp; chipotle crema on the side.</p>
    </div>

    <h2 class="section-title" style="left:24px;top:318px">WING-FULL NACHOS</h2>
    <div class="abs nacho-box"><p>Tortilla chips, melted white queso, Cheddar and Monterey Jack cheeses, pico de gallo, guacamole, chipotle sour cream, jalapenos, black beans, &amp; green onions</p></div>
    <div class="opt nacho-opt" style="left:24px;top:396px">Copper Moth Chili Nachos<span class="price" style="left:104px;top:0">14</span></div>
    <div class="opt nacho-opt" style="left:145px;top:396px">Pulled Chicken Nachos<span class="price" style="left:94px;top:0">16</span></div>
    <div class="opt nacho-opt" style="left:12px;top:414px"><span class="tick tick--gold"></span>Fire Roasted<br><span style="padding-left:14px">Vegetables Nachos</span><span class="price" style="left:104px;top:0">14</span></div>
    <div class="opt nacho-opt" style="left:145px;top:414px">Garlic Roasted Shrimp<span class="price" style="left:94px;top:0">16</span></div>

    <h2 class="section-title" style="left:26px;top:440px;font-size:14px">WINGS</h2>
    <div class="art" style="left:119px;top:425px;width:50px;height:47px;background:radial-gradient(circle,#e88a7c,var(--red))" role="img" aria-label="Sketch of a chicken drumstick"></div>
    <div class="art" style="left:217px;top:463px;width:36px;height:12px;background:radial-gradient(ellipse,#b32a1c,var(--red))" role="img" aria-label="Sketch of a chili pepper"></div>
    <div class="opt" style="left:28px;top:467px">8 Pieces <span class="price" style="position:static">14</span></div>
    <p class="abs wings-desc">Flash-fried to a crispy golden brown and tossed in your choice of sauce. Choose from our Signature Hot, or Mild Sauce, or BBQ. Your choice of ranch or blue cheese.</p>
  </div>

  <div class="panel panel--fries">
    <div class="abs fries-frame"></div>
    <div class="abs fries-box">
      <h2 class="section-title" style="left:9px;top:10px;font-size:12.5px">FRENCH FRIES</h2>
      <p class="abs fries-note">Served with our house made Garlic Aioli and Spicy Ketchup</p>
      <div class="opt" style="left:4px;top:41px"><span class="tick tick--gold"></span>Fries Only<span class="price" style="left:81px;top:0">7</span></div>
      <div class="opt" style="left:4px;top:60px"><span class="tick tick--gold"></span>Cheddar-Jack<br><span style="padding-left:14px">Cheese Fries</span><span class="price" style="left:81px;top:2px">8</span></div>
      <div class="opt" style="left:10px;top:88px">Chili Cheese Fries<span class="price" style="left:75px;top:0">10</span></div>
      <p class="abs" style="left:10px;top:103px;width:88px;font-size:6.3px;line-height:1.05;color:var(--yellow)">Topped with Copper Moth Chili, cheddar jack cheese and served with chipotle crema on the side</p>
      <div class="opt" style="left:99px;top:41px"><span class="tick tick--gold"></span>Sweet<br><span style="padding-left:14px">Potato Fries</span><span class="price" style="left:64px;top:0">7</span></div>
      <div class="opt" style="left:113px;top:70px">Cheddar-<br>Jack Cheese,<br>Bacon Fries<span class="price" style="left:50px;top:0">9</span></div>
    </div>

    <div class="banner" style="left:22px;top:188px;width:154px;height:71px;background:var(--blue);color:var(--yellow);font-size:26px;text-align:left;padding:12px 0 0 16px;line-height:.95">SOUPS &amp;<br>BOWLS</div>
    <div class="art" style="left:180px;top:190px;width:75px;height:71px;background:radial-gradient(circle,#e2e0f0,#fff)" role="img" aria-label="Line sketch of a soup bowl with a spoon"></div>

    <div class="soup" style="top:284px">
      <div class="soup__head">Copper Moth Chili<span class="leader"></span>Cup 6 | Bowl 8</div>
      <p class="soup__desc">Copper Moth Signature Chili with lean ground beef, black beans, &amp; corn. Topped with cheddar cheese and green onion, served with tri-color tortilla chips.</p>
    </div>
    <div class="soup" style="top:329px">
      <div class="soup__head" style="font-size:11.5px"><span class="tick"></span>Southwestern Sweet Potato Soup<span class="leader"></span>Cup 6 | Bowl 8</div>
      <p class="soup__desc">A mix of sweet potatoes, corn, bell peppers, and black beans, this vegan soup delivers top flavor &amp; quality with every bowl. Served with tri-color tortilla chips.</p>
    </div>
    <div class="soup" style="top:374px">
      <div class="soup__head">Ancient Grains Bowl<span class="leader"></span>12</div>
      <p class="soup__desc">Quinoa, brown rice, kale and fresh spinach, with fire roasted portobello mushrooms, zucchini and red peppers. Topped with fresh avocado, and feta cheese. Served with Lemon Champagne Vinaigrette</p>
    </div>

    <div class="abs soup-add"><span>Add:</span><em>Grilled Chicken 5 | Garlic Roasted Shrimp 5</em></div>
    <div class="abs notice"><p>* The consumption of raw or undercooked eggs, meat, poultry, seafood or shellfish may contribute to food borne illness, especially if you have a medical condition.</p></div>
  </div>

</section>
</body>
</html>
```